A clean crisp business card for a Landscape Construction company. Designed to be easy to read contact/ info and also be appealing/interesting, unlike a traditional business card.

Industry/Entity Type

Landscape Construction

Contact Information for Business Card

Company name : Brambleford Landscape Construction, phone number: (877) 62Vista, website:Bramblefordyards.example, Email, sales@bramblefordyards.example

Requirements
Nice to have
• Luxurious finishes/ details…. Icons or emblems next to contact info
Should not have
• Clipart or general pictures

```html
<!DOCTYPE html>
<html lang="en">
<head>
<meta charset="utf-8">
<title>Brambleford Landscape Construction – Business Card</title>
<link href="https://fonts.googleapis.com/css2?family=Montserrat:wght@600;700&family=Arimo:wght@400&display=swap" rel="stylesheet">
<style>
  :root {
    --stage: #2b2b2b;
    --card-black: #050505;
    --card-white: #ffffff;
    --brand-green: #8cc63f;
    --brand-green-light: #a6d65a;
    --brand-blue: #1a66c4;
    --ink: #2a2a2a;
  }
  * { box-sizing: border-box; margin: 0; padding: 0; }
  html, body { width: 1200px; height: 900px; overflow: hidden; }
  body {
    background: var(--stage);
    font-family: "Arimo", Arial, sans-serif;
    position: relative;
  }
  .card {
    position: absolute;
    left: 250px;
    width: 700px;
    height: 400px;
    border-radius: 4px;
    overflow: hidden;
    box-shadow: 0 12px 30px rgba(0,0,0,.55);
  }
  .card--front { top: 40px; background: var(--card-black); }
  .card--back { top: 470px; background: var(--card-white); }

  .wordmark {
    display: flex;
    align-items: center;
    gap: 14px;
    font-family: "Montserrat", sans-serif;
    font-weight: 600;
    color: var(--brand-blue);
  }
  .wordmark__dot {
    flex: none;
    border-radius: 50%;
    background: var(--brand-green);
  }
  .card--front .wordmark {
    position: absolute; inset: 0; justify-content: center;
    font-size: 34px; line-height: 1.15;
    color: var(--brand-green);
  }
  .card--front .wordmark__dot { width: 30px; height: 30px; }

  .card--back .wordmark {
    position: absolute; left: 40px; top: 90px; width: 240px;
    font-size: 24px; line-height: 1.2;
  }
  .card--back .wordmark__dot { width: 22px; height: 22px; }

  .divider {
    position: absolute; left: 300px; top: 40px;
    width: 3px; height: 210px; background: var(--brand-blue);
  }
  .contact { position: absolute; left: 340px; top: 48px; width: 340px; color: var(--ink); }
  .contact__name {
    font-family: "Montserrat", sans-serif; font-weight: 700;
    font-size: 28px; color: var(--brand-green);
  }
  .contact__role { font-size: 16px; letter-spacing: 1px; margin: 2px 0 20px 6px; }
  .contact__row { display: flex; gap: 14px; font-size: 14px; line-height: 1.45; margin-bottom: 14px; }
  .contact__icon { flex: none; width: 18px; height: 18px; margin-top: 2px; }
  .contact__lines { display: flex; flex-direction: column; }

  .site {
    position: absolute; right: 40px; top: 268px;
    font-size: 17px; color: var(--ink); letter-spacing: .3px;
  }
  .decor-band {
    position: absolute; left: 0; right: 0; bottom: 0; height: 90px;
    background: linear-gradient(90deg, var(--brand-blue) 0%, var(--brand-green) 55%, var(--brand-green-light) 100%);
  }
</style>
</head>
<body>

  <section class="card card--front" aria-label="Card front">
    <div class="wordmark">
      <span class="wordmark__dot"></span>
      <span>Brambleford<br>Landscape Construction</span>
    </div>
  </section>

  <section class="card card--back" aria-label="Card back">
    <div class="wordmark">
      <span class="wordmark__dot"></span>
      <span>Brambleford Landscape Construction</span>
    </div>

    <div class="divider"></div>

    <div class="contact">
      <div class="contact__name">Owen Hartwell</div>
      <div class="contact__role">CEO</div>

      <div class="contact__row">
        <svg class="contact__icon" viewBox="0 0 24 24" aria-hidden="true">
          <path d="M12 2a7 7 0 0 0-7 7c0 5 7 13 7 13s7-8 7-13a7 7 0 0 0-7-7zm0 9.5A2.5 2.5 0 1 1 12 6.5a2.5 2.5 0 0 1 0 5z" fill="var(--brand-green)"/>
        </svg>
        <div class="contact__lines">
          <span>4120 Alder Creek Rd.,</span>
          <span>NUM 118, Millbrook, OH 45990</span>
        </div>
      </div>

      <div class="contact__row">
        <svg class="contact__icon" viewBox="0 0 24 24" aria-hidden="true">
          <path d="M6.6 10.8a15 15 0 0 0 6.6 6.6l2.2-2.2a1 1 0 0 1 1-.25 11.4 11.4 0 0 0 3.6.57 1 1 0 0 1 1 1V20a1 1 0 0 1-1 1A17 17 0 0 1 3 4a1 1 0 0 1 1-1h3.5a1 1 0 0 1 1 1c0 1.25.2 2.45.57 3.57a1 1 0 0 1-.25 1z" fill="var(--brand-green)"/>
        </svg>
        <span>(877) 62Vista</span>
      </div>

      <div class="contact__row">
        <svg class="contact__icon" viewBox="0 0 24 24" aria-hidden="true">
          <rect x="2" y="5" width="20" height="14" rx="1.5" fill="var(--brand-green)"/>
          <path d="M3 6l9 7 9-7" fill="none" stroke="#fff" stroke-width="1.6"/>
        </svg>
        <span>sales@bramblefordyards.example</span>
      </div>
    </div>

    <div class="site">www.bramblefordyards.example</div>

    <div class="decor-band" role="img" aria-label="Green and blue flowing wave band with a leaf accent along the bottom of the card"></div>
  </section>

</body>
</html>
```